Business Card Design Project

The business card is for an educational company that provides personalised tuition to students.

The company logo is in orange and blue (as provided) and should be included in the name card design

The philosophy of the company is to make learning a comfortable experience for student as such design of the namecard should look fresh and has a bit of the 'wow' factor. Some of the namecard design that appeals to me are as uploaded under Sample Design.

The particulars that need to be provided are:
(1): Company Name (Lantern Education)
(1): Name
(2): Educational qualifications which will appear below name
(3): Mobile number
(4): Email address
(5): Website

Industry/Entity Type

Business

Requirements
Must have
• (1): Company Logo

(2): The card background should preferably be coloured both for the front side and back.

(3): The choice of font is important as part of the selection consideration. There is no preferred font that I have selected, designer is free to choose the font that will complement their design.

```html
<!DOCTYPE html>
<html lang="en">
<head>
<meta charset="utf-8">
<title>Lantern Education – Business Card</title>
<link rel="stylesheet" href="https://fonts.googleapis.com/css2?family=Libre+Baskerville:wght@700&family=Noto+Sans:wght@400;700&display=swap">
<style>
  :root {
    --stage: #d9d9d9;
    --card-cream: #fbf8ef;
    --card-white: #ffffff;
    --floral-gold: rgba(230,217,168,0.55);
    --floral-gold-deep: rgba(210,192,124,0.45);
    --bird-green: rgba(169,178,58,0.55);
    --bird-pink: rgba(217,66,111,0.55);
    --ink: #2b2b2b;
    --ink-soft: #3d3d3d;
    --mark-orange: #f07a1c;
  }
  * { box-sizing: border-box; margin: 0; padding: 0; }
  html, body { width: 1200px; height: 861px; overflow: hidden; }
  body {
    background: var(--stage);
    position: relative;
    font-family: "Noto Sans", Arial, sans-serif;
    color: var(--ink);
  }
  .card {
    position: absolute;
    top: 262px;
    width: 510px;
    height: 310px;
    border-radius: 16px;
    overflow: hidden;
    background: radial-gradient(ellipse at 55% 40%, var(--card-white) 0%, var(--card-cream) 55%, #efe8d2 100%);
    box-shadow: 0 6px 18px rgba(0,0,0,0.18);
  }
  .card--front { left: 75px; }
  .card--back  { left: 620px; }

  .floral-pattern {
    position: absolute;
    inset: 0;
    background:
      radial-gradient(circle at 20% 80%, var(--floral-gold) 0, rgba(230,217,168,0) 28%),
      radial-gradient(circle at 75% 18%, var(--floral-gold) 0, rgba(230,217,168,0) 26%),
      radial-gradient(circle at 85% 85%, var(--floral-gold-deep) 0, rgba(210,192,124,0) 30%),
      radial-gradient(circle at 45% 95%, var(--floral-gold) 0, rgba(230,217,168,0) 22%);
  }
  .bird-illustration {
    position: absolute;
    background: radial-gradient(closest-side, var(--bird-pink) 0%, var(--bird-green) 55%, rgba(169,178,58,0) 100%);
  }
  .card--front .bird-illustration { left: 0; top: 10px; width: 250px; height: 240px; }
  .card--back  .bird-illustration { right: 0; top: 15px; width: 160px; height: 130px; }

  .brand {
    position: absolute;
    display: flex;
    align-items: center;
    gap: 10px;
  }
  .brand__square {
    width: 62px; height: 62px;
    background: var(--mark-orange);
    border-radius: 4px;
    flex: none;
  }
  .brand__name {
    font-family: "Libre Baskerville", Georgia, serif;
    font-weight: 700;
    font-size: 25px;
    line-height: 1.1;
    color: var(--ink-soft);
  }
  .card--front .brand { left: 270px; top: 122px; }
  .card--front .website {
    position: absolute;
    left: 305px; top: 195px;
    font-size: 14px; font-weight: 700;
  }
  .card--back .brand { left: 70px; top: 54px; }
  .card--back .brand__square { width: 72px; height: 72px; }
  .card--back .brand__name { font-size: 29px; }

  .person { position: absolute; left: 72px; top: 158px; }
  .person__name {
    font-family: "Libre Baskerville", Georgia, serif;
    font-weight: 700;
    font-size: 26px;
    white-space: nowrap;
  }
  .person__degrees { font-size: 12px; font-weight: 700; }
  .person__role { font-size: 15px; margin-top: 0; }

  .contacts {
    position: absolute; left: 72px; top: 224px;
    font-size: 14px; line-height: 22px;
    border-collapse: collapse;
  }
  .contacts th { text-align: left; font-weight: 700; padding-right: 8px; }
  .contacts td { font-weight: 400; }
</style>
</head>
<body>
  <section class="card card--front" aria-label="Card front">
    <div class="floral-pattern" role="img" aria-label="Faint gold floral paisley pattern"></div>
    <div class="bird-illustration" role="img" aria-label="Decorative batik-style dove with pink and green plumes"></div>
    <div class="brand">
      <span class="brand__square"></span>
      <span class="brand__name">Lantern<br>Education</span>
    </div>
    <p class="website">www.lantern-edu.com</p>
  </section>

  <section class="card card--back" aria-label="Card back">
    <div class="floral-pattern" role="img" aria-label="Faint gold floral paisley pattern"></div>
    <div class="bird-illustration" role="img" aria-label="Decorative batik-style dove with pink and green plumes"></div>
    <div class="brand">
      <span class="brand__square"></span>
      <span class="brand__name">Lantern<br>Education</span>
    </div>
    <div class="person">
      <p class="person__name">Tan Wei Ming <span class="person__degrees">PhD, Bsc (Hons)</span></p>
      <p class="person__role">Senior Tutor</p>
    </div>
    <table class="contacts">
      <tr><th>Mobile</th><td>: +65 91234567</td></tr>
      <tr><th>Email</th><td>: wmtan@lantern-edu.com</td></tr>
      <tr><th>Website</th><td>: www.lantern-edu.com</td></tr>
    </table>
  </section>
</body>
</html>
```